Animal Eye Clinic needs a Business card

We are a new veterinary ophthalmology practice (Ridgeline Pet Vision Care) and we need a business card designed. We only see animal eyes - we are not a regular veterinary clinic. We already have a logo. We are looking for a professional, good looking business card to hand out to our clients. We are looking for something simple but professional and contemporary. Our logo is likely the only picture/graphic that needs to be on the card.
Updates

Contact Information for Business Card

Delia Vossman, BSc, DVM, MSc, DipACVO
Veterinary Ophthalmologist

Phone: 250.418.3927
Email: ridgelinepetvisioncare@mailbox-example.net
Website: ridgelinepetvisioncare-example.net
Address: 1874 Thornbury Rd
Kelowna, BC, V1X 4M9

Colors

Designer to choose colors to be used in the design.

Requirements
Must have
• Our logo (attached)

```html
<!DOCTYPE html>
<html lang="en">
<head>
<meta charset="utf-8">
<title>Ridgeline Pet Vision Care – Business Card</title>
<link href="https://fonts.googleapis.com/css2?family=Roboto:wght@400;500;700&display=swap" rel="stylesheet">
<style>
  :root {
    --teal: #1b97a6;
    --charcoal: #242223;
    --ink: #4a4a4a;
    --paper: #ffffff;
    --backdrop: #d9dadc;
  }
  * { box-sizing: border-box; margin: 0; padding: 0; }
  html, body { width: 1200px; height: 800px; overflow: hidden; }
  body {
    background: var(--backdrop);
    font-family: "Roboto", Arial, sans-serif;
    position: relative;
  }
  .card {
    position: absolute;
    left: 290px;
    width: 620px;
    height: 354px;
    overflow: hidden;
    box-shadow: 0 6px 18px rgba(0,0,0,0.18);
  }

  /* Front */
  .card--front { top: 30px; background: var(--charcoal); }
  .front-art {
    position: absolute; right: 0; top: 0;
    width: 330px; height: 354px;
    z-index: 0;
  }
  .front-brand {
    position: absolute; left: 42px; top: 112px;
    z-index: 1;
    color: var(--teal);
    font-weight: 500;
    font-size: 26px;
    line-height: 1.15;
    letter-spacing: 1px;
    text-transform: uppercase;
  }
  .front-url {
    position: absolute; left: 42px; top: 238px;
    z-index: 1;
    color: var(--paper);
    font-size: 14px;
    letter-spacing: 2px;
    white-space: nowrap;
  }

  /* Back */
  .card--back { top: 416px; background: var(--paper); }
  .brand {
    position: absolute; left: 44px; top: 34px;
    display: flex; align-items: center; gap: 16px;
  }
  .brand-dot {
    width: 46px; height: 46px; border-radius: 50%;
    background: var(--teal);
  }
  .brand-name {
    color: var(--teal);
    font-weight: 500;
    font-size: 25px;
    letter-spacing: 1px;
    text-transform: uppercase;
    line-height: 1.15;
  }
  .person { position: absolute; left: 44px; top: 140px; right: 0; }
  .person-name {
    color: var(--teal);
    font-weight: 700;
    font-size: 22px;
    text-transform: uppercase;
  }
  .person-name .credentials {
    font-size: 15px;
    text-transform: none;
  }
  .person-title-row { display: flex; align-items: center; gap: 6px; margin-top: 2px; }
  .person-title { color: var(--ink); font-size: 17px; white-space: nowrap; }
  .rule { flex: 1; height: 2px; background: var(--teal); margin-top: 8px; }
  .contacts {
    position: absolute; left: 44px; top: 228px;
    list-style: none;
    color: var(--ink);
    font-size: 15px;
    line-height: 1.5;
  }
  .contacts li { display: flex; align-items: center; gap: 8px; }
  .contacts svg { width: 13px; height: 13px; fill: var(--teal); flex: none; }
  .address {
    position: absolute; right: 38px; bottom: 24px;
    color: var(--ink);
    font-size: 16px;
    line-height: 1.35;
    text-align: right;
  }
</style>
</head>
<body>

  <section class="card card--front">
    <svg class="front-art" viewBox="0 0 330 354" role="img" aria-label="Illustration of horse, dog and cat silhouettes in teal and charcoal">
      <path d="M150 354 C 130 300, 112 255, 104 222 C 150 200, 175 150, 215 90 L 260 45 L 330 32 L 330 354 Z" fill="var(--teal)"/>
    </svg>
    <div class="front-brand">Ridgeline<br>Pet Vision Care</div>
    <div class="front-url">ridgelinepetvisioncare-example.net</div>
  </section>

  <section class="card card--back">
    <div class="brand">
      <span class="brand-dot"></span>
      <span class="brand-name">Ridgeline<br>Pet Vision Care</span>
    </div>

    <div class="person">
      <div class="person-name">Delia Vossman <span class="credentials">BSc, DVM, MSc, DipACVO</span></div>
      <div class="person-title-row">
        <span class="person-title">Veterinary Ophthalmologist</span>
        <span class="rule"></span>
      </div>
    </div>

    <ul class="contacts">
      <li>
        <svg viewBox="0 0 24 24"><path d="M6.6 10.8a15.1 15.1 0 0 0 6.6 6.6l2.2-2.2a1 1 0 0 1 1-.25 11.4 11.4 0 0 0 3.6.57 1 1 0 0 1 1 1V20a1 1 0 0 1-1 1A17 17 0 0 1 3 4a1 1 0 0 1 1-1h3.5a1 1 0 0 1 1 1c0 1.25.2 2.450.57 3.570a1 1 0 0 1-.25 1z"/></svg>
        250.418.3927
      </li>
      <li>
        <svg viewBox="0 0 24 24"><path d="M2 5h20v14H2z M4 7v.4l8 5.3 8-5.3V7z" fill-rule="evenodd"/></svg>
        ridgelinepetvisioncare@mailbox-example.net
      </li>
      <li>
        <svg viewBox="0 0 24 24"><circle cx="12" cy="12" r="10"/></svg>
        ridgelinepetvisioncare-example.net
      </li>
    </ul>

    <div class="address">1874 Thornbury Rd<br>Kelowna, BC, V1X 4M9</div>
  </section>

</body>
</html>
```